Nursing Concepts Diagram

We are looking to make a diagram to represent the Conceptual Framework of our nursing program (college). The frame work is based on three parts:

I. Nursing Process

II. Core Concepts
a. Clinical Competence
b. Critical Thinking
c. Moral/Ethical Principles
d. Growth Mindset
e. Caring/Compassion
f. Cultural Competence
g. Effective Communication
h. Life-long Learning

III. Tavrin's Hierarchy of Needs

I have attached two sketches to give you a sense of how I think this could work.

Please also consider the following:

-Tavrin's Hierarchy of Needs is always represented in the shape of a pyramid so I think the other two components (Nursing Process and Core Concepts) should complement that.

Target Market(s)

Healthcare Professionals, Nursing Educators

Font styles to use
Sans Serif

Colors

Designer to choose colors to be used in the design.

Requirements
Must have
• We would like the diagram to include a legend somewhere on the paper that outlines the parts of each component like demonstrated in the attached table
• All the small parts of the Nursing Process and Tavrin's Hierarchy of Needs don't need to be listed out in the diagram because it may look too wordy, but the eight parts that make up the core concepts should all be listed
• The Nursing Process and Tavrin's Hierachy of needs should both border each of the 8 core concepts so that it can show a relation.

```html
<!DOCTYPE html>
<html lang="en">
<head>
<meta charset="utf-8">
<title>Nursing Program Conceptual Framework</title>
<link rel="stylesheet" href="https://fonts.googleapis.com/css2?family=Montserrat:wght@500;600;700&family=Oswald:wght@500;600&display=swap">
<style>
  :root {
    --bg-center: #f0f0f0;
    --bg-edge: #cfcfd0;
    --ring-white: #ffffff;
    --core-grey: #a9a9a9;
    --title-red: #e8202a;
    --lifelong: #c8c23a;
    --cultural: #22780c;
    --clinical: #b40a0e;
    --critical: #0b6a8a;
    --moral: #f07020;
    --communication: #050505;
    --growth: #6ec0b0;
    --caring: #a8a8a8;
    --esteem: #ed1c24;
    --safety: #0d6384;
    --selfact: #c8c23a;
    --love: #00a651;
    --physio: #404040;
    --legend-head: #3b3b3b;
    --legend-text: #333333;
  }
  * { margin: 0; padding: 0; box-sizing: border-box; }
  html, body { width: 1200px; height: 927px; overflow: hidden; }
  body {
    background: radial-gradient(ellipse at 50% 45%, var(--bg-center) 0%, #e2e2e3 55%, var(--bg-edge) 100%);
    font-family: "Montserrat", Arial, sans-serif;
    position: relative;
  }
  .framework { position: absolute; left: 0; top: 0; width: 1200px; height: 700px; }
  .segment-label {
    font-family: "Montserrat", Arial, sans-serif;
    font-weight: 600; font-size: 19px; letter-spacing: 1px;
    fill: #fff; text-anchor: middle;
  }
  .hierarchy-title {
    font-family: "Montserrat", Arial, sans-serif;
    font-weight: 700; font-size: 37px; letter-spacing: 1.5px;
    fill: var(--title-red);
  }
  .tier-label {
    font-family: "Montserrat", Arial, sans-serif;
    font-weight: 600; font-size: 14.5px; letter-spacing: 1px;
    fill: #fff; text-anchor: middle;
  }
  .legend-column { position: absolute; top: 720px; }
  .legend-heading {
    font-family: "Oswald", "Arial Narrow", sans-serif;
    font-weight: 600; font-size: 18px; color: var(--legend-head);
    letter-spacing: 0.3px; margin-bottom: 16px; height: 22px;
  }
  .legend-list { list-style: none; }
  .legend-list li {
    position: relative; padding-left: 18px;
    font-size: 10.5px; font-weight: 500; color: var(--legend-text);
    height: 24px; line-height: 14px;
  }
  .legend-list li::before {
    content: ""; position: absolute; left: 0; top: 2px;
    width: 10px; height: 10px; border-radius: 50%; background: #3a3a3a;
  }
  .legend-list li::after {
    content: ""; position: absolute; left: 2.5px; top: 5px;
    width: 3px; height: 3px;
    border-top: 1.5px solid #fff; border-right: 1.5px solid #fff;
    transform: rotate(45deg);
  }
  .legend-nursing { left: 26px; }
  .legend-core { left: 347px; }
  .legend-core-extra { left: 567px; top: 758px; }
  .legend-needs { left: 850px; }
</style>
</head>
<body>
<svg class="framework" viewBox="0 0 1200 700" width="1200" height="700" aria-label="Conceptual framework diagram">
  <defs>
    <path id="title-arc" d="M414.56 439.92 A200 200 0 1 1 785.44 439.92"/>
  </defs>

  <g class="core-concepts">
    <path fill="var(--cultural)" d="M613.49 43.28 A322 322 0 0 1 817.96 127.98 L755.68 195.70 A230 230 0 0 0 609.63 135.20 Z"/>
    <path fill="var(--clinical)" d="M837.02 147.04 A322 322 0 0 1 921.72 351.51 L829.80 355.37 A230 230 0 0 0 769.30 209.32 Z"/>
    <path fill="var(--critical)" d="M921.72 378.49 A322 322 0 0 1 837.02 582.96 L769.30 520.68 A230 230 0 0 0 829.80 374.63 Z"/>
    <path fill="var(--moral)" d="M817.96 602.02 A322 322 0 0 1 613.49 686.72 L609.63 594.80 A230 230 0 0 0 755.68 534.30 Z"/>
    <path fill="var(--communication)" d="M586.51 686.72 A322 322 0 0 1 382.04 602.02 L444.32 534.30 A230 230 0 0 0 590.37 594.80 Z"/>
    <path fill="var(--growth)" d="M362.98 582.96 A322 322 0 0 1 278.28 378.49 L370.20 374.63 A230 230 0 0 0 430.70 520.68 Z"/>
    <path fill="var(--caring)" d="M278.28 351.51 A322 322 0 0 1 362.98 147.04 L430.70 209.32 A230 230 0 0 0 370.20 355.37 Z"/>
    <path fill="var(--lifelong)" d="M382.04 127.98 A322 322 0 0 1 586.51 43.28 L590.37 135.20 A230 230 0 0 0 444.32 195.70 Z"/>
  </g>

  <g class="core-concept-labels">
    <text class="segment-label" transform="translate(705.6 110) rotate(22.5)"><tspan x="0" y="-6">CULTURAL</tspan><tspan x="0" y="17">COMPETENCE</tspan></text>
    <text class="segment-label" transform="translate(855 259.4) rotate(67.5)"><tspan x="0" y="-6">CLINICAL</tspan><tspan x="0" y="17">COMPETENCE</tspan></text>
    <text class="segment-label" transform="translate(855 470.6) rotate(-67.5)"><tspan x="0" y="-6">CRITICAL</tspan><tspan x="0" y="17">THINKING</tspan></text>
    <text class="segment-label" transform="translate(705.6 620) rotate(-22.5)"><tspan x="0" y="-6">MORAL/ETHICAL</tspan><tspan x="0" y="17">PRINCIPLES</tspan></text>
    <text class="segment-label" transform="translate(494.4 620) rotate(22.5)"><tspan x="0" y="-6">EFFECTIVE</tspan><tspan x="0" y="17">COMMUNICATION</tspan></text>
    <text class="segment-label" transform="translate(345 470.6) rotate(67.5)"><tspan x="0" y="-6">GROWTH</tspan><tspan x="0" y="17">MINDSET</tspan></text>
    <text class="segment-label" transform="translate(345 259.4) rotate(-67.5)"><tspan x="0" y="-6">CARING/</tspan><tspan x="0" y="17">COMPASSION</tspan></text>
    <text class="segment-label" transform="translate(494.4 110) rotate(-22.5)"><tspan x="0" y="-6">LIFE-LONG</tspan><tspan x="0" y="17">LEARNING</tspan></text>
  </g>

  <circle class="hierarchy-ring" cx="600" cy="365" r="237" fill="var(--ring-white)"/>
  <circle class="hierarchy-core" cx="600" cy="366" r="181" fill="var(--core-grey)"/>

  <text class="hierarchy-title"><textPath href="#title-arc" startOffset="50%" text-anchor="middle">TAVRIN'S HIERARCHY OF NEEDS</textPath></text>

  <g class="nursing-pyramid" stroke="#d9d9d9" stroke-width="1">
    <polygon fill="var(--esteem)" points="595,185 656.5,287 533.5,287"/>
    <polygon fill="var(--safety)" points="533.5,287 656.5,287 688.5,340 501.5,340"/>
    <polygon fill="var(--selfact)" points="501.5,340 688.5,340 719.8,392 470.2,392"/>
    <polygon fill="var(--love)" points="470.2,392 719.8,392 752.4,446 437.6,446"/>
    <polygon fill="var(--physio)" points="437.6,446 752.4,446 785,500 405,500"/>
  </g>
  <g class="tier-labels">
    <text class="tier-label" x="595" y="265">ESTEEM</text>
    <text class="tier-label" x="595" y="319">SAFETY NEEDS</text>
    <text class="tier-label" x="595" y="371">SELF-ACTUALIZATION</text>
    <text class="tier-label" x="595" y="424">LOVE AND BELONGING</text>
    <text class="tier-label" x="595" y="478">PHYSIOLOGICAL NEEDS</text>
  </g>
</svg>

<section class="legend-column legend-nursing">
  <h2 class="legend-heading">NURSING PROCESS</h2>
  <ul class="legend-list">
    <li>Assessment</li>
    <li>Nursing Diagnosis</li>
    <li>Planning</li>
    <li>Intervention</li>
    <li>Evaluation</li>
  </ul>
</section>

<section class="legend-column legend-core">
  <h2 class="legend-heading">CORE CONCEPTS</h2>
  <ul class="legend-list">
    <li>Clinical Competence</li>
    <li>Critical Thinking</li>
    <li>Moral/Ethical Principles</li>
    <li>Growth Mindset</li>
    <li>Caring/Compassion</li>
  </ul>
</section>

<section class="legend-column legend-core-extra">
  <ul class="legend-list">
    <li>Cultural Competence</li>
    <li>Effective Communication</li>
    <li>Life-long Learning</li>
  </ul>
</section>

<section class="legend-column legend-needs">
  <h2 class="legend-heading">TAVRIN'S HIERARCHY OF NEEDS</h2>
  <ul class="legend-list">
    <li>Self-actualization</li>
    <li>Esteem</li>
    <li>Love and Belonging</li>
    <li>Safety Needs</li>
    <li>Physiological Needs</li>
  </ul>
</section>
</body>
</html>
```